Business Card for Polygraph business in Africa

Business Card . Polygraph Examiner based in Tanzania, East Africa.
Business Card will be used to disseminate contact information to potential clients.
It should convey that I am a professional specifically in the polygraph field and perform my work with integrity.

I have attached the business card that I'm currently using, which I threw together myself initially. It's not professional enough.

Target Market(s)

Banks, Accounting Firms, Government Ministries, Gas, Oil, & Gemstone Mining Concerns, Wildlife Conservation NGOs, International companies located in East Africa.

Industry/Entity Type

Business

Contact Information for Business Card

Veritrace Kilonga
Miriam Holloway
PO Box 48317
Arusha, Tanzania
+255 612 839 274
miriamholloway@postvale.example

Colors
00a990
f37122
faa54b

Requirements
Must have
• - Veritrace Kilonga (with the word "Polygraph" being more prominent than the word "Tanzania")
• - Forensic Examinations
• - Employment Screening
• - Should contain a logo of the Continental Truthline Society (of which I'm a member)
• - I would like an accent design (such as the polygraph "squiggles" of a cardio tracing or such as that)
• - My contact information (less prominent, but large enough to read legibly). I would also consider putting the contact information on the second side of the card.
Nice to have
• My color suggestions are changeable.
Should not have
• Anything "cutesy" or "cartoonish"

```html
<!DOCTYPE html>
<html lang="en">
<head>
<meta charset="utf-8">
<title>Veritrace Kilonga – Business Card</title>
<link rel="stylesheet" href="https://fonts.googleapis.com/css2?family=Roboto:wght@400;500&family=Roboto+Condensed:wght@500;700&display=swap">
<style>
  :root {
    --backdrop: #2b2b2d;
    --brand-blue: #0b4592;
    --card-white: #f2f2f2;
    --text-light: #ffffff;
    --text-grey: #4a4a4a;
  }
  * { margin: 0; padding: 0; box-sizing: border-box; }
  html, body { width: 1200px; height: 960px; overflow: hidden; }
  body { background: var(--backdrop); font-family: "Roboto", Arial, sans-serif; position: relative; }

  .card {
    position: absolute;
    width: 600px;
    height: 342px;
    border-radius: 18px;
    overflow: hidden;
    background: var(--card-white);
  }
  .card-front { left: 314px; top: 114px; background: var(--brand-blue); }
  .card-back { left: 311px; top: 473px; }

  .front-panel { position: absolute; inset: 0; }

  .front-brand {
    position: absolute; left: 330px; right: 10px; top: 150px;
    text-align: center;
    font-family: "Roboto", Arial, sans-serif; font-weight: 500;
    font-size: 30px; line-height: 40px;
    color: var(--brand-blue);
  }

  .membership-badge { position: absolute; left: 34px; top: 32px; width: 90px; height: 90px; }

  .holder { position: absolute; left: 33px; top: 146px; color: var(--text-light); }
  .holder-name { font-family: "Roboto Condensed", Arial, sans-serif; font-weight: 700; font-size: 21px; line-height: 26px; }
  .holder-company { font-family: "Roboto", Arial, sans-serif; font-weight: 500; font-size: 15px; line-height: 20px; }

  .address { position: absolute; left: 33px; top: 210px; color: var(--text-light); font-size: 14.5px; line-height: 19px; font-style: normal; }

  .contacts { position: absolute; left: 33px; top: 255px; list-style: none; color: var(--text-light); font-size: 14.5px; line-height: 19.5px; }
  .contacts li { display: flex; align-items: center; gap: 9px; }
  .contacts svg { width: 13px; height: 13px; flex: none; fill: var(--text-light); }

  .brand-name {
    position: absolute; left: 0; right: 0; top: 144px;
    text-align: center;
    font-family: "Roboto", Arial, sans-serif; font-weight: 500;
    font-size: 42px; line-height: 50px;
    color: var(--brand-blue);
  }
  .services {
    position: absolute; left: 0; right: 0; top: 287px;
    display: flex; justify-content: center; align-items: center; gap: 9px;
    font-size: 14.5px; color: var(--text-grey);
  }
  .services .divider { width: 7px; height: 7px; border-radius: 50%; background: var(--brand-blue); }
</style>
</head>
<body>

<section class="card card-front" aria-label="Business card front">
  <svg class="front-panel" viewBox="0 0 600 342" aria-hidden="true">
    <ellipse cx="475" cy="171" rx="158" ry="180" fill="var(--card-white)"/>
    <rect x="475" y="0" width="125" height="342" fill="var(--card-white)"/>
  </svg>

  <p class="front-brand">Veritrace Kilonga</p>

  <svg class="membership-badge" viewBox="0 0 90 90" role="img" aria-label="Continental Truthline Society membership badge">
    <circle cx="45" cy="45" r="44" fill="var(--text-light)"/>
    <circle cx="45" cy="45" r="38" fill="var(--brand-blue)"/>
    <circle cx="45" cy="45" r="25" fill="none" stroke="var(--text-light)" stroke-width="1.5"/>
  </svg>

  <div class="holder">
    <p class="holder-name">Miriam Holloway</p>
    <p class="holder-company">Veritrace Kilonga</p>
  </div>

  <address class="address">
    PO Box 48317<br>
    Arusha, Tanzania
  </address>

  <ul class="contacts">
    <li>
      <svg viewBox="0 0 24 24" aria-hidden="true"><path d="M6.6 10.8a15.1 15.1 0 0 0 6.6 6.6l2.2-2.2c.3-.3.7-.4 1-.2 1.1.4 2.3.6 3.6.6.6 0 1 .4 1 1V20c0 .6-.4 1-1 1A17 17 0 0 1 3 4c0-.6.4-1 1-1h3.5c.6 0 1 .4 1 1 0 1.3.2 2.5.6 3.6.1.3 0 .7-.2 1z"/></svg>
      <span>+255 612 839 274</span>
    </li>
    <li>
      <svg viewBox="0 0 24 24" aria-hidden="true"><path d="M2 6.5V19h20V6.5l-10 7z M2 5h20l-10 7z"/></svg>
      <span>miriamholloway@postvale.example</span>
    </li>
    <li>
      <svg viewBox="0 0 24 24" aria-hidden="true"><path d="M12 2a10 10 0 1 0 0 20 10 10 0 0 0 0-20zm6.9 6h-2.9a15.7 15.7 0 0 0-1.4-3.6A8 8 0 0 1 18.9 8zM12 4c.8 1.2 1.5 2.5 1.9 4h-3.8c.4-1.5 1.1-2.8 1.9-4zM4.3 14a8 8 0 0 1 0-4h3.4a16.5 16.5 0 0 0 0 4zm.8 2h2.9c.3 1.3.8 2.5 1.4 3.6A8 8 0 0 1 5.1 16zM8 8H5.1a8 8 0 0 1 4.3-3.6C8.8 5.5 8.3 6.7 8 8zm4 12c-.8-1.2-1.5-2.5-1.9-4h3.8c-.4 1.5-1.1 2.8-1.9 4zm2.3-6H9.7a14.7 14.7 0 0 1 0-4h4.6a14.7 14.7 0 0 1 0 4zm.3 5.6c.6-1.1 1.1-2.300 1.4-3.6h2.9a8 8 0 0 1-4.3 3.6zm1.7-5.6a16.5 16.5 0 0 0 0-4h3.4a8 8 0 0 1 0 4z"/></svg>
      <span>www.miriamholloway.example</span>
    </li>
  </ul>
</section>

<section class="card card-back" aria-label="Business card back">
  <h1 class="brand-name">Veritrace Kilonga</h1>
  <p class="services">
    <span>Forensic Examinations</span>
    <span class="divider" aria-hidden="true"></span>
    <span>Employment Screening</span>
  </p>
</section>

</body>
</html>
```